Oral Surgeon Referral Pads

Hello. We need referral pads for Dr Elsabet Quorvane, DDS board certified oral surgeon's new office - Harrowgate Dunmere Oral & Maxillofacial Surgery. See logo uploaded. See some images we would like included
Updates

Designs look the same

Font styles to use
Serif
Script

Colors
00AB8E
00BBA5
67D7C9
C6EFE9
E9F9F6

Requirements
Must have
• Color Pantone 623c. Also foldable business cards

```html
<!DOCTYPE html>
<html lang="en">
<head>
<meta charset="utf-8">
<title>Referral for Oral Surgery – Harrowgate Dunmere</title>
<link rel="stylesheet" href="https://fonts.googleapis.com/css2?family=Sorts+Mill+Goudy&family=Libre+Baskerville&family=Lato:wght@400&display=swap">
<style>
  :root{
    --navy:#002b63;
    --ink:#333333;
    --paper:#ffffff;
    --backdrop:#d6d6d6;
    --serif:"Sorts Mill Goudy", Georgia, serif;
    --title:"Libre Baskerville", Georgia, serif;
    --sans:"Lato", Arial, sans-serif;
  }
  *{box-sizing:border-box;margin:0;padding:0}
  html,body{width:1082px;height:1200px;overflow:hidden;background:var(--backdrop)}
  .sheet{
    position:absolute;left:91px;top:18px;width:1240px;height:1605px;
    transform:scale(.725);transform-origin:0 0;
    background:var(--paper);font-family:var(--serif);color:var(--ink);
  }
  .side-band{position:absolute;left:0;top:0;width:120px;height:1605px}
  .brand{position:absolute;left:90px;top:78px;width:420px;text-align:center;color:var(--navy);font-family:var(--serif)}
  .brand-dot{width:70px;height:70px;border-radius:50%;background:var(--navy);margin:0 auto 26px}
  .brand-name{font-size:40px;line-height:48px}
  .brand-sub{font-size:27px;line-height:36px}
  .contact-rule{position:absolute;left:789px;top:82px;width:3px;height:208px;background:var(--navy)}
  .contact{position:absolute;left:832px;top:80px;font-family:var(--sans);font-size:20px;letter-spacing:1px;color:var(--ink)}
  .contact li{list-style:none;display:flex;align-items:flex-start;height:29.5px}
  .contact li.addr{height:66px}
  .contact svg{width:20px;height:20px;margin:2px 20px 0 0;flex:none;fill:var(--navy)}
  .contact span{line-height:30px}
  .title-pill{position:absolute;left:225px;top:354px;width:829px;height:65px;border-radius:33px;background:var(--navy);
    color:#fff;font-family:var(--title);font-size:38px;letter-spacing:6px;text-align:center;line-height:66px}
  .row{position:absolute;left:107px;width:1065px;display:flex;align-items:baseline;font-size:22px;line-height:30px;white-space:nowrap}
  .fill{flex:1;border-bottom:2px dotted #555;margin:0 2px;transform:translateY(-5px)}
  .box{display:inline-block;width:18px;height:18px;border:2px solid #333;margin:0 7px 0 13px;transform:translateY(2px)}
  .box.first{margin-left:0}
  .section-head{position:absolute;left:107px;top:686px;font-size:25px;text-decoration:underline;text-underline-offset:4px;color:var(--ink)}
  .reasons{position:absolute;top:740px;font-size:22px;line-height:30.5px}
  .reasons li{list-style:none}
  .reasons .box{margin:0 15px 0 0}
  .chart{position:absolute;left:0;top:0;width:1240px;height:1605px;font-size:22px;letter-spacing:1px}
  .chart span{position:absolute;transform:translate(-50%,-50%)}
  .chart .side{font-size:28px}
  .chart .hline{position:absolute;left:295px;top:1111px;width:682px;height:2px;background:#333}
  .chart .vline{position:absolute;left:623px;top:1030px;width:2px;height:166px;background:#333}
  .notes{position:absolute;left:107px;top:1390px;width:1090px;color:var(--navy)}
  .notes h3{font-weight:400;font-size:20px;text-decoration:underline;text-underline-offset:3px;margin-bottom:12px}
  .notes p{font-size:19px;line-height:27px}
  .notes h4{font-weight:400;font-size:20px;margin-top:30px;margin-left:-3px}
  .notes .warn{font-size:24px;line-height:26px;margin-left:-3px}
</style>
</head>
<body>
<div class="sheet">
  <svg class="side-band" viewBox="0 0 120 1605" aria-hidden="true">
    <path d="M0 0 H30 C65 100 80 250 76 400 C70 650 20 900 25 1200 C28 1380 60 1500 95 1605 H0 Z" fill="var(--navy)"/>
  </svg>

  <div class="brand">
    <div class="brand-dot"></div>
    <div class="brand-name">Harrowgate Dunmere</div>
    <div class="brand-sub">Oral &amp; Maxillofacial Surgery</div>
  </div>

  <div class="contact-rule"></div>
  <ul class="contact">
    <li class="addr"><svg viewBox="0 0 20 20"><path d="M10 1a6 6 0 0 0-6 6c0 4.5 6 12 6 12s6-7.5 6-12a6 6 0 0 0-6-6zm0 8.5A2.5 2.5 0 1 1 10 4.5a2.5 2.5 0 0 1 0 5z"/></svg><span>417 Corvell Lane<br>Brenholt, CT 06999</span></li>
    <li><svg viewBox="0 0 20 20"><path d="M4 2l3 0 2 5-2 1.5a11 11 0 0 0 4.5 4.5L13 11l5 2v3c0 1-1 2-2 2C9 18 2 11 2 4c0-1 1-2 2-2z"/></svg><span>(555) 014-2207</span></li>
    <li><svg viewBox="0 0 20 20"><path d="M6 1h8a1 1 0 0 1 1 1v16a1 1 0 0 1-1 1H6a1 1 0 0 1-1-1V2a1 1 0 0 1 1-1zm1 2v11h6V3zm3 12.5a1 1 0 1 0 0 2 1 1 0 0 0 0-2z"/></svg><span>(555) 014-2208</span></li>
    <li><svg viewBox="0 0 20 20"><path d="M5 1h10v5H5zM2 7h16a1 1 0 0 1 1 1v7h-4v4H5v-4H1V8a1 1 0 0 1 1-1zm5 7v3h6v-3z"/></svg><span>(555) 014-2209</span></li>
    <li><svg viewBox="0 0 20 20"><path d="M1 4h18v1.5l-9 6-9-6zm0 3.5l9 6 9-6V16H1z"/></svg><span>care@harrowgatedunmere.com</span></li>
    <li><svg viewBox="0 0 20 20"><path d="M10 1a9 9 0 1 0 0 18 9 9 0 0 0 0-18zm-1 3c-2 1-3 3-2 4s3 0 3 2-2 2-1 4 2 3 1 4a7 7 0 0 1-1-14zm3 0a7 7 0 0 1 5 8c-1-1-2 0-3-1s0-3-1-4-2-1-1-3z"/></svg><span>www.harrowgatedunmere.com</span></li>
  </ul>

  <div class="title-pill">REFERRAL FOR ORAL SURGERY</div>

  <div class="row" style="top:457px">Presenting<span class="fill"></span>Date of Birth<span class="fill"></span></div>
  <div class="row" style="top:512px">Date<span class="fill" style="flex:.62"></span>Patient Phone Number<span class="fill"></span></div>
  <div class="row" style="top:567px">Radiographs:<span class="box"></span>With Patient<span class="box"></span>Mailed<span class="box"></span>Emailed</div>
  <div class="row" style="top:621px">Should We Contact Patient To Schedule?<span class="box"></span>Yes<span class="box"></span>No</div>

  <div class="section-head">REASON FOR REFERRAL</div>
  <ul class="reasons" style="left:107px">
    <li><span class="box"></span>Extraction/Surgical Removal</li>
    <li><span class="box"></span>Uncovery/Exposure</li>
    <li><span class="box"></span>Apical Surgery</li>
  </ul>
  <ul class="reasons" style="left:536px">
    <li><span class="box"></span>Pathology</li>
    <li><span class="box"></span>Trauma/Facial Fracture</li>
    <li><span class="box"></span>Cleft Palate</li>
  </ul>
  <ul class="reasons" style="left:921px">
    <li><span class="box"></span>Implant Consult</li>
    <li><span class="box"></span>Orthognathic Consult</li>
    <li><span class="box"></span>TMJ Consult</li>
  </ul>

  <div class="row" style="top:855px">Comments<span class="fill"></span></div>
  <div class="row" style="top:913px"><span class="fill"></span></div>
  <div class="row" style="top:968px"><span class="fill"></span></div>

  <div class="chart" aria-label="Tooth chart">
    <span style="left:455px;top:1045px">A</span><span style="left:489px;top:1045px">B</span><span style="left:524px;top:1045px">C</span><span style="left:560px;top:1045px">D</span><span style="left:595px;top:1045px">E</span>
    <span style="left:651px;top:1045px">F</span><span style="left:685px;top:1045px">G</span><span style="left:722px;top:1045px">H</span><span style="left:754px;top:1045px">I</span><span style="left:780px;top:1045px">J</span>
    <span style="left:313px;top:1077px">1</span><span style="left:351px;top:1077px">2</span><span style="left:391px;top:1077px">3</span><span style="left:431px;top:1077px">4</span><span style="left:472px;top:1077px">5</span><span style="left:514px;top:1077px">6</span><span style="left:556px;top:1077px">7</span><span style="left:594px;top:1077px">8</span>
    <span style="left:649px;top:1077px">9</span><span style="left:692px;top:1077px">10</span><span style="left:735px;top:1077px">11</span><span style="left:782px;top:1077px">12</span><span style="left:826px;top:1077px">13</span><span style="left:872px;top:1077px">14</span><span style="left:918px;top:1077px">15</span><span style="left:963px;top:1077px">16</span>
    <span class="side" style="left:274px;top:1112px">R</span><span class="side" style="left:997px;top:1112px">L</span>
    <div class="hline"></div><div class="vline"></div>
    <span style="left:307px;top:1146px">32</span><span style="left:349px;top:1146px">31</span><span style="left:390px;top:1146px">30</span><span style="left:430px;top:1146px">29</span><span style="left:469px;top:1146px">28</span><span style="left:509px;top:1146px">27</span><span style="left:546px;top:1146px">26</span><span style="left:586px;top:1146px">25</span>
    <span style="left:655px;top:1146px">24</span><span style="left:697px;top:1146px">23</span><span style="left:738px;top:1146px">22</span><span style="left:780px;top:1146px">21</span><span style="left:818px;top:1146px">20</span><span style="left:858px;top:1146px">19</span><span style="left:895px;top:1146px">18</span><span style="left:936px;top:1146px">17</span>
    <span style="left:455px;top:1180px">T</span><span style="left:488px;top:1180px">S</span><span style="left:522px;top:1180px">R</span><span style="left:557px;top:1180px">Q</span><span style="left:591px;top:1180px">P</span>
    <span style="left:654px;top:1180px">O</span><span style="left:691px;top:1180px">N</span><span style="left:730px;top:1180px">M</span><span style="left:766px;top:1180px">L</span><span style="left:800px;top:1180px">K</span>
  </div>

  <div class="row" style="top:1219px">Referring Doctor<span class="fill"></span></div>
  <div class="row" style="top:1274px">Office Phone<span class="fill"></span>May We communicate Via Email?<span class="box" style="margin-left:6px"></span>Yes<span class="box" style="margin-left:6px"></span>No</div>
  <div class="row" style="top:1328px">If yes, Email Address<span class="fill"></span></div>

  <div class="notes">
    <h3>FOR ALL PATIENTS:</h3>
    <p>Please Bring this referral with you. / If you take prescription medications, check with your surgeon for day of surgery instructions. / If you do not have a consultation prior to your surgery and plan on having treatment on your first visit to the office, please verify your insurance prior to your appointment. Bring all insurance ID cards to your appointment.</p>
    <h4>FOR PATIENTS HAVING SEDATION / GENERAL ANESTHESIA (ASLEEP FOR YOUR SURGERY)</h4>
    <div class="warn">Do not eat or drink anything, including water, within 6 hours of your appointment</div>
  </div>
</div>
</body>
</html>
```